Silver Harbor Staffing Agency

I need to make a brochure/catalogue that represent our company, telling our clients what we do, our values, fields of industry that we taken care of, so they know who we are, what we did, and how we do it.
I do have a logo and simple brochure design before that i really need to upgrade (i will give it as an example on this attachment).

What I want in the new design is :
1. More pictures and little bit of explanation in each industry we work with.
2. Attractive design that make people LOOK at the brochure and not just throw it in the trash.
3. Still use the combination color of the company logo itself, which is Golden Brown.

```html
<!DOCTYPE html>
<html lang="en">
<head>
<meta charset="utf-8">
<title>Silver Harbor Staffing Agency – Brochure</title>
<link rel="stylesheet" href="https://fonts.googleapis.com/css2?family=Montserrat:ital,wght@0,400;0,500;0,600;0,700;0,800;1,600;1,700&display=swap">
<style>
:root{
  --paper:#ffffff;
  --ink:#1c1c1c;
  --gold:#b5913e;
  --gold-text:#c9a24a;
  --white:#ffffff;
  --soft:#e8e8e8;
}
*{margin:0;padding:0;box-sizing:border-box}
html,body{width:800px;height:1200px;overflow:hidden;background:var(--paper)}
body{position:relative;font-family:'Montserrat',sans-serif;color:var(--white)}
.spread{position:absolute;left:177px;width:446px;height:335px;background:var(--ink);overflow:hidden;box-shadow:0 1px 4px rgba(0,0,0,.25)}
.spread-cover{top:51px}
.spread-inside{top:436px}
.spread-back{top:821px}
.abs{position:absolute}
.heading{position:absolute;z-index:2;font-weight:700;font-size:7px;letter-spacing:.2px;color:var(--gold-text);line-height:1}
.heading::after{content:"";display:block;width:20px;height:.8px;background:var(--gold-text);margin-top:1.5px}
.body{position:absolute;font-size:4.1px;line-height:5.4px;text-align:justify;color:var(--soft)}
.item-title{position:absolute;font-weight:600;font-size:5.8px;line-height:1;color:var(--white)}
.photo{position:absolute;border:1px solid var(--white)}
.brand-name{position:absolute;display:flex;align-items:center;gap:2px;font-weight:700;color:var(--gold-text);white-space:nowrap}
.brand-dot{border-radius:50%;background:var(--gold-text)}
.location-map{position:absolute;left:48px;top:111px;width:84px;height:108px;background:#ffffff;border-radius:4px}
.state-label{position:absolute;z-index:2;font-weight:700;font-size:6px;line-height:1;color:var(--white);white-space:nowrap}
.contact-line{position:absolute;display:flex;align-items:flex-start;gap:3px;font-size:4.3px;line-height:5px;color:var(--soft)}
.contact-phone{font-weight:700;font-size:6.6px;line-height:7px;color:var(--white)}
.cover-slogan{position:absolute;left:247px;top:250px;font-weight:800;font-size:16px;line-height:19px;color:var(--white);letter-spacing:.5px}
.cover-slogan .accent{color:var(--gold-text)}
.cover-url{position:absolute;left:247px;top:311px;font-size:5px;color:var(--white)}
.cover-url b{font-weight:700}
.mission-band{position:absolute;left:0;top:135px;width:223px;height:65px;background:var(--gold)}
.mission-band .body{color:var(--white)}
.tagline-band{position:absolute;left:0;top:314px;width:446px;height:21px}
.tagline-left{position:absolute;left:13px;top:4px;font-weight:800;font-size:12.6px;letter-spacing:.3px;color:var(--white)}
.tagline-left span{color:var(--gold-text)}
.tagline-right{position:absolute;left:223px;top:0;width:223px;height:21px;background:var(--gold);font-weight:800;font-size:12.6px;letter-spacing:.3px;color:var(--ink);padding:4px 0 0 19px;white-space:nowrap}
.intro-italic{position:absolute;font-weight:700;font-style:italic;font-size:4.1px;line-height:5.4px;text-align:justify;color:var(--white)}
</style>
</head>
<body>

<section class="spread spread-cover">
  <svg class="abs" style="left:0;top:0" width="446" height="335" viewBox="0 0 874 656" aria-hidden="true">
    <polygon points="0,157 601,157 455,295 601,440 0,440" fill="#b5913e"/>
    <polygon points="478,295 790,0 820,0 520,295 870,656 835,656" fill="#2a2a2a"/>
    <polyline points="798,0 500,295 855,656" fill="none" stroke="#b5913e" stroke-width="5"/>
  </svg>
  <div class="abs" role="img" aria-label="Photo: businessman climbing stairs toward a sunlit city skyline"
       style="left:0;top:0;width:446px;height:335px;clip-path:polygon(410px 0,446px 0,446px 335px,434px 335px,258px 151px);background:linear-gradient(160deg,#f2a65a 0%,#e8c79a 25%,#9aa3a8 55%,#5f6b73 100%)"></div>

  <div class="heading" style="left:13px;top:15px">INDUSTRIES</div>
  <p class="body" style="left:13px;top:31px;width:190px">Need industry-leading talent for your organization? Career options that are ideal for your skills and experience? The professionals at Silver Harbor Staffing have the tools and knowledge to help you make the perfect match.</p>

  <div class="brand-name" style="left:258px;top:38px;font-size:6px"><span class="brand-dot" style="width:7px;height:7px"></span>SILVER HARBOR Inc.</div>

  <div class="heading" style="left:15px;top:97px;color:var(--white);font-size:8px">OUR LOCATION</div>
  <div class="location-map" role="img" aria-label="Map of the eastern United States highlighting the served states"></div>
  <svg class="abs" style="left:0;top:0" width="446" height="335" aria-hidden="true">
    <g stroke="#ffffff" stroke-width=".6">
      <line x1="125" y1="118" x2="144" y2="116"/>
      <line x1="122" y1="124" x2="144" y2="125"/>
      <line x1="122" y1="128" x2="144" y2="132"/>
      <line x1="117" y1="140" x2="144" y2="140"/>
      <line x1="113" y1="148" x2="144" y2="148"/>
    </g>
  </svg>
  <div class="state-label" style="left:146px;top:113px">New York</div>
  <div class="state-label" style="left:146px;top:122px">Pennsylvania</div>
  <div class="state-label" style="left:146px;top:129px">New jersey</div>
  <div class="state-label" style="left:146px;top:137.5px">Delaware</div>
  <div class="state-label" style="left:146px;top:145px">Verginia</div>

  <div class="brand-name" style="left:13px;top:236px;font-size:4.5px"><span class="brand-dot" style="width:5px;height:5px"></span>SILVER HARBOR Inc.</div>

  <div class="heading" style="left:13px;top:265px">CONTACT FORM</div>
  <p class="body" style="left:13px;top:278px;width:82px;text-align:left">Thank you for choosing Silver Harbor Staffing. If you have temporary jobs you are hiring for please get in touch with Silver Harbor Staffing. We are able to help with all your staffing and employment needs.</p>

  <div class="heading" style="left:107px;top:266px">CONTACT INFO</div>
  <div class="contact-line" style="left:107px;top:278px">
    <svg width="5" height="6" viewBox="0 0 10 12" aria-hidden="true"><path d="M2 1 L4 1 L5 4 L3.5 5 Q5 8 7 9 L8 7.5 L10 9 L10 11 Q5 11 2 6 Q0.5 3 2 1Z" fill="#c9a24a"/></svg>
    <span class="contact-phone">555-204-7318</span>
  </div>
  <div class="contact-line" style="left:107px;top:289px">
    <svg width="4" height="6" viewBox="0 0 8 12" aria-hidden="true"><path d="M4 0 A4 4 0 0 1 8 4 Q8 7 4 12 Q0 7 0 4 A4 4 0 0 1 4 0Z M4 2.5 A1.5 1.5 0 1 0 4 5.5 A1.5 1.5 0 1 0 4 2.5Z" fill="#c9a24a" fill-rule="evenodd"/></svg>
    <span>48 Harbor Ln, suite 210<br>Bayview, NJ 08000</span>
  </div>
  <div class="contact-line" style="left:107px;top:303px">
    <svg width="5" height="4" viewBox="0 0 10 8" aria-hidden="true"><rect x=".5" y=".5" width="9" height="7" fill="#c9a24a"/><polyline points=".5,.5 5,4.5 9.5,.5" fill="none" stroke="#1c1c1c" stroke-width="1"/></svg>
    <span>hello@silverharborstaffing.com</span>
  </div>
  <div class="contact-line" style="left:107px;top:312px">
    <svg width="5" height="5" viewBox="0 0 10 10" aria-hidden="true"><circle cx="5" cy="5" r="4.4" fill="none" stroke="#c9a24a" stroke-width="1"/><ellipse cx="5" cy="5" rx="2" ry="4.4" fill="none" stroke="#c9a24a" stroke-width=".8"/><line x1=".6" y1="5" x2="9.4" y2="5" stroke="#c9a24a" stroke-width=".8"/></svg>
    <span>www.silverharborstaffing.com</span>
  </div>

  <h1 class="cover-slogan">YOUR<br>BEST WAY<br>TO <span class="accent">SUCCEED</span></h1>
  <div class="cover-url">www.<b>silverharborstaffing</b>.com</div>
</section>

<section class="spread spread-inside">
  <div class="heading" style="left:13px;top:15px">ABOUT US</div>
  <p class="body" style="left:13px;top:25px;width:192px">With more than 18 years of experience Silver Harbor Staffing provided staffing services to a wide array of locations, all throughout Pennsylvania. Through the last few years we have expanded to 5 other states including New York, New Jersey, Delaware, Virginia and Georgia. Our ethics are a critical building block of our business. Our own success is based on adherence to the highest ethical standards; long-term client relationships, the ability to identify top candidates, and the high-quality professional development of Silver Harbor Staffing professionals protecting the confidentiality and interests of clients and candidates.</p>

  <div class="heading" style="left:13px;top:79px">CULTURE</div>
  <p class="body" style="left:13px;top:89px;width:192px">Silver Harbor Staffing believes in equal opportunity for all, regardless of gender, race, ethic, origin, religion, or handicap. The staffing policies and practices of Silver Harbor Staffing for our organization, our clients and candidates are fully non-discriminatory. Our employees are our most valuable asset. We strive to create a work environment of professionalism, trust and respect that will continuously provide our staff with motivation, challenge, and professional growth to aim our most important goal; CLIENT SATISFACTION.</p>

  <div class="mission-band">
    <div class="heading" style="left:13px;top:6px;color:var(--ink)">MISSION</div>
    <p class="body" style="left:13px;top:16px;width:192px">Silver Harbor Staffing is more than a staffing company; we want to become your business partner. We understand that payroll and employee-service overhead can be one of the largest expenses for your business. Through our partnership-network programs Silver Harbor Staffing can help you reduce the hard-costs of your business expenses. We take responsibility for all our placed employees, including payroll taxes and benefits allowing you to focus on running your business.</p>
  </div>

  <div class="heading" style="left:13px;top:209px">OUR PROCESS</div>
  <p class="body" style="left:13px;top:219px;width:192px">Our screening process includes a thorough interview with each potential candidate to give us insight into the candidate's previous work history, skills, communication abilities and career goals as well as reference checks with their previous employers.</p>

  <div class="heading" style="left:13px;top:249px">OUR SERVICES</div>
  <p class="body" style="left:13px;top:262px;width:108px">Silver Harbor Staffing's personalized services, expertise and affordable rates are key factors of our success and being our client's choice staffing agency. Our contingent and contract-to-hire employees are looking for flexible careers in New York, New Jersey, Pennsylvania, Delaware, Virginia and Georgia.</p>
  <div class="photo" role="img" aria-label="Photo: smiling manager in shirt and tie in a warehouse" style="left:132px;top:247px;width:79px;height:50px;background:linear-gradient(135deg,#8a6a48,#c9a57a 50%,#d9d6d0)"></div>

  <div class="heading" style="left:243px;top:15px">INDUSTRIES WE SERVE:</div>

  <div class="item-title" style="left:243px;top:30px">Warehousing</div>
  <p class="body" style="left:243px;top:37px;width:95px">Are one of our Staffing company strengths. We are able to provide warehouse workers that responsible for performing an array of duties such as receiving and processing incoming stock and materials, picking and filling orders from stock, packing and shipping orders, or managing, organizing, and retrieving stock and others.</p>
  <div class="photo" role="img" aria-label="Photo: warehouse worker in hard hat and safety vest between shelves" style="left:347px;top:31px;width:76px;height:41px;background:linear-gradient(135deg,#7a5a44,#b9a27e 50%,#d7d27a)"></div>

  <div class="photo" role="img" aria-label="Photo: hotel housekeeper holding folded towels in a corridor" style="left:244px;top:93px;width:76px;height:41px;background:linear-gradient(135deg,#5b4536,#a78a6e 50%,#e6e0d8)"></div>
  <div class="item-title" style="left:332px;top:93px">Hotel</div>
  <p class="body" style="left:332px;top:100px;width:91px">Whether you are travelling for business or pleasure, the luxury hotel services offered by the five star Grand Meridian Hotel make it an ideal choice for your stay in Riga, Latvia.</p>

  <div class="item-title" style="left:243px;top:143px">Farming</div>
  <p class="body" style="left:243px;top:150px;width:95px">Agriculture Industries is one of Silver Harbor Staffing's biggest partners all these years. The other capability that not many staffing companies can provide yet ours able to provide you with temporary staffing that you need. Please contact your Executive Agent today for more information.</p>
  <div class="photo" role="img" aria-label="Photo: farm worker harvesting green crops" style="left:347px;top:149px;width:76px;height:41px;background:linear-gradient(135deg,#3f5a22,#7fa04a 55%,#b6c47a)"></div>

  <div class="photo" role="img" aria-label="Photo: worker carrying rolled paper in a mailing facility" style="left:244px;top:203px;width:76px;height:41px;background:linear-gradient(135deg,#6a6e74,#c8ccd0 55%,#eeeeee)"></div>
  <div class="item-title" style="left:332px;top:204px">Paper Mailling</div>
  <p class="body" style="left:332px;top:211px;width:91px">Our paper mailing courier sacks have become popular with businesses and organisations looking for sustainable alternatives to polythene mailing bags.</p>

  <div class="item-title" style="left:243px;top:251px">Landfill</div>
  <p class="body" style="left:243px;top:258px;width:96px">Landfill gas is produced by wet organic waste decomposing under anaerobic conditions in a landfill. Landfills gas production is dependant, on the degradation status of the waste material as well as moisture and temperature, all of which may vary greatly in different parts of the landfill body.</p>
  <div class="photo" role="img" aria-label="Photo: worker in red safety vest driving a forklift" style="left:348px;top:256px;width:76px;height:41px;background:linear-gradient(135deg,#6b4a32,#b08560 50%,#c23a2a 80%,#8a6a4a)"></div>

  <div class="tagline-band">
    <div class="tagline-left">CONNECTING <span>OPPORTUNITY</span></div>
    <div class="tagline-right">WITH TODAY'S TOP TALENT</div>
  </div>
</section>

<section class="spread spread-back">
  <div class="heading" style="left:13px;top:15px">WHY STAFFING ?</div>

  <div class="item-title" style="left:13px;top:29px">Avoid Unemployment Claims</div>
  <p class="body" style="left:13px;top:36px;width:108px">The temporary staff personnel is an employee of the staffing agency and not the business, there is no concern about the person filing for unemployment when their services are no longer needed by the business reducing overall operating and human resources costs.</p>
  <div class="photo" role="img" aria-label="Photo: hand signing a document with a pen" style="left:128px;top:27px;width:70px;height:50px;background:linear-gradient(135deg,#9fb3c6,#e4e8ec 55%,#d8b89a)"></div>

  <div class="photo" role="img" aria-label="Photo: hand touching a rising digital bar chart" style="left:13px;top:82px;width:70px;height:50px;background:linear-gradient(135deg,#dfe7ef,#5d86b3 55%,#2f4f7a)"></div>
  <div class="item-title" style="left:93px;top:92px">Improve Productivity</div>
  <p class="body" style="left:93px;top:99px;width:108px">By bringing in temporary staff to handle the extra work-load, your full-time employees can continue to focus on their main job tasks while maintaining their productivity.</p>

  <div class="item-title" style="left:13px;top:147px">Increasing Flexibility</div>
  <p class="body" style="left:13px;top:154px;width:108px">Temporary employees can be brought in to cover the vacation of an employee or maternity leave or a seasonal work. Whether it is a few hours a week or on a full-time basis, using a staffing agency can avoid the permanent commitment that a full-time employee requires.</p>
  <div class="photo" role="img" aria-label="Photo: young plant growing from a stack of coins" style="left:128px;top:142px;width:70px;height:50px;background:linear-gradient(135deg,#cfe3b0,#7da84a 55%,#c9c2a8)"></div>

  <div class="photo" role="img" aria-label="Photo: stacked coins beside financial charts and a pencil" style="left:13px;top:201px;width:70px;height:50px;background:linear-gradient(135deg,#f2f2f2,#c8c0ae 55%,#8f8673)"></div>
  <div class="item-title" style="left:93px;top:207px">Decrease Cost</div>
  <p class="body" style="left:93px;top:214px;width:108px">Employing temporary staff can decrease overhead costs such as overtime for regular, fulltime employees as well as additional benefits that the business does not have to provide to a temporary staff member.</p>

  <div class="item-title" style="left:13px;top:263px">Contract To Hire</div>
  <p class="body" style="left:13px;top:270px;width:108px">Reduce the risk of making a bad hire by evaluating a candidate's performance in your work environment. You can choose to add workers to your permanent team or requesting another worker for your evaluation.</p>
  <div class="photo" role="img" aria-label="Photo: business people shaking hands across a desk" style="left:128px;top:257px;width:70px;height:50px;background:linear-gradient(135deg,#f0f0f0,#b9bcc0 55%,#3a3d42)"></div>

  <div class="heading" style="left:241px;top:15px">WHY CHOOSE OUR SERVICES ?</div>
  <p class="intro-italic" style="left:241px;top:27px;width:189px">Our commitment is to deliver the highest possible level of service, professionalism and integrity. Our focus is on delivering results and building long term client relationships by providing top quality candidates.</p>

  <div class="item-title" style="left:241px;top:56px">Employee Benefits</div>
  <p class="body" style="left:241px;top:63px;width:108px">Workers are paid on a timely weekly basis. Our system responds to worker's need for payment immediately.</p>
  <div class="photo" role="img" aria-label="Photo: team meeting around a table in a bright office" style="left:358px;top:47px;width:70px;height:50px;background:linear-gradient(135deg,#f4f4f2,#c7cbc4 55%,#6e7f6a)"></div>

  <div class="photo" role="img" aria-label="Photo: construction workers on steel scaffolding against the sky" style="left:242px;top:103px;width:70px;height:50px;background:linear-gradient(135deg,#8fb0d4,#c9d6e3 50%,#7a6a58)"></div>
  <div class="item-title" style="left:321px;top:109px">Workers' Compensation</div>
  <p class="body" style="left:321px;top:117px;width:108px">We provide workers' compensation for our employees while on assignment. If an injury occurs, we handle all claims and expenses. Our safety and risk department will help reduce injuries and will ensure high rates of safety compliance.</p>

  <div class="item-title" style="left:241px;top:170px">Availability and Flexibility</div>
  <p class="body" style="left:241px;top:177px;width:108px">Our temporary staff has proven to be available and ready for work in a timely and efficient manner. Our services will be crafted to your needs and specifications ensuring that you are not forced into any unnecessary liabilities.</p>
  <div class="photo" role="img" aria-label="Photo: warehouse staff in safety vests reviewing a laptop" style="left:358px;top:162px;width:70px;height:50px;background:linear-gradient(135deg,#b08a62,#d8c7a8 50%,#d7d86a)"></div>

  <div class="item-title" style="left:241px;top:227px">We Save you both TIME and MONEY</div>
  <p class="body" style="left:241px;top:235px;width:189px">Competitive rates to keep your business on budget. We bill only for employee's hours approved by you. Our business was built on a strong reputation for providing quality service. Part of that reputation stems from an unmatched focus on developing a deep understanding of the job market. We do our best to keep up to date on industry trends, job market patterns, and hiring practices. We believe that knowledge is a driving factor in staffing agency success, and we work with our clients and candidates so they are in the best position possible to accomplish their employment goals.</p>

  <p class="intro-italic" style="left:241px;top:289px;width:189px">When you are looking for a qualified candidate or when you need a new job, trust the experts at Silver Harbor Staffing Services. Let us put our world-class customer service and staffing expertise to work for you!</p>

  <div class="tagline-band">
    <div class="tagline-left">CONNECTING <span>OPPORTUNITY</span></div>
    <div class="tagline-right">WITH TODAY'S TOP TALENT</div>
  </div>
</section>

</body>
</html>
```